NZ First of it's kind solutions directory and marketplace for busy Mums needs a business card design

We need a business card design for our new nationwide business in NZ (long term plans to go global). We provide solutions to the everyday challenges that busy Mums face by connecting them with quality communities and suppliers of carefully selected, relevant products and services. We sell direct via our online marketplace. The final design should communicate our values of inclusivity, quality and smart solutions. Colours should incorporate our logo colour palette of #477077 and #6ba8b2. Our website is at https://www.brightnestmums.example

Target Market(s)

busy Mums, Age 28 – 50, female, income over $100K, location main centres NZ primarily but NZ wide. Is likely juggling work or career with a young family. Probably had hobbies which have fallen by the wayside.
-Wants to succeed in her chosen career without compromising on family life
-to successfully juggle her career without feeling like she is compromising her children
- Is time poor, something always has to give and it’s generally her health (she’ll stay up late, get stressed)
- probably ex corporate or professional career. Has discretional income

Industry/Entity Type

Business

Contact Information for Business Card

Lena Forbisher, Founder, BrightNestMums.example (Strapline Tap; Gather; Sorted), 47 Kowhai Terrace, Ellerslie, Auckland 1051, New Zealand. Mob: 021 483 517 Ph: +64 (0)9 571 4860

Font styles to use
Other font styles liked:
• Raleway, and/or Architects Daughter

Colors
00a990
33b8a4
86cfc6
cfeae6

Requirements
Must have
• the above details, streamline. the logo and colours associated with those logos
Should not have
• foil or metallic colours

```html
<!DOCTYPE html>
<html lang="en">
<head>
<meta charset="utf-8">
<title>BrightNestMums — Business Card</title>
<link rel="stylesheet" href="https://fonts.googleapis.com/css2?family=Work+Sans:wght@400;500;600&display=swap">
<style>
  :root {
    --brand-dark: #477077;
    --brand-light: #6ba8b2;
    --text-muted: #3f5f64;
    --backdrop: #e0e0e0;
    --card-white: #ffffff;
    --photo-warm: #8a6a4e;
    --photo-grey: #5d5e60;
  }
  * { margin: 0; padding: 0; box-sizing: border-box; }
  html, body {
    width: 1200px; height: 897px; overflow: hidden;
    background: var(--backdrop);
    font-family: "Work Sans", Arial, sans-serif;
  }
  .stage { position: relative; width: 1200px; height: 897px; }
  .card {
    position: absolute; left: 303px; width: 595px; height: 339px; overflow: hidden;
  }
  .card--front { top: 92px; background: var(--card-white); }
  .card--back { top: 469px; }

  .brand {
    position: absolute; left: 0; right: 0;
    display: flex; align-items: center; justify-content: center; gap: 12px;
    font-weight: 600; letter-spacing: -0.5px;
  }
  .brand__dot { width: 30px; height: 30px; border-radius: 50%; }
  .card--front .brand { top: 64px; font-size: 36px; color: var(--brand-dark); }
  .card--front .brand__dot { background: var(--brand-light); }

  .person { position: absolute; top: 166px; left: 0; right: 0; text-align: center; }
  .person__name { font-size: 26px; font-weight: 500; color: var(--brand-light); line-height: 1.1; }
  .person__role { font-size: 14.5px; color: var(--text-muted); letter-spacing: 1px; margin-top: 3px; }
  .person__rule { width: 64px; height: 1px; background: var(--brand-dark); margin: 13px auto 0; }

  .contact {
    position: absolute; top: 243px; left: 0; right: 0; text-align: center;
    font-size: 14.5px; line-height: 23px; letter-spacing: 0.9px; color: var(--brand-dark);
  }
  .contact__label { color: var(--brand-light); }

  .back-photo {
    position: absolute; inset: 0;
    background:
      radial-gradient(ellipse at 45% 30%, #b08560 0%, var(--photo-warm) 30%, transparent 65%),
      linear-gradient(180deg, #6b6664 0%, var(--photo-grey) 100%);
  }
  .card--back .brand { top: 146px; font-size: 42px; color: #ffffff; }
  .card--back .brand__dot { background: #ffffff; }
  .back-web {
    position: absolute; top: 296px; left: 0; right: 0; text-align: center;
    font-size: 15px; letter-spacing: 1px; color: #ffffff;
  }
</style>
</head>
<body>
<main class="stage">
  <section class="card card--front">
    <div class="brand"><span class="brand__dot"></span><span class="brand__name">BrightNestMums</span></div>
    <div class="person">
      <p class="person__name">Lena Forbisher</p>
      <p class="person__role">Founder</p>
      <div class="person__rule"></div>
    </div>
    <div class="contact">
      <p><span class="contact__label">M :</span> 021 483 517 | <span class="contact__label">P :</span> +64 (0)9 571 4860</p>
      <p><span class="contact__label">W :</span> www.brightnestmums.example</p>
      <p><span class="contact__label">A :</span> 47 Kowhai Terrace, Ellerslie Auckland 1051, New Zealand</p>
    </div>
  </section>

  <section class="card card--back">
    <div class="back-photo" role="img" aria-label="Photo of a tired mother resting her face on her hands, warm soft-focus tones"></div>
    <div class="brand"><span class="brand__dot"></span><span class="brand__name">BrightNestMums</span></div>
    <p class="back-web">www.brightnestmums.example</p>
  </section>
</main>
</body>
</html>
```